Birchline Septic Solutions

Would like to see some single sided ones but would also like to see some double sided with one sided only being the logo. Owners name is Colin Vandro. Phone number is 555-214-0387
Services are pumping, inspections, installs, and repairs

Contact Information for Business Card

555-241-0387 Colin Vandro Harlow Springs, OH

```html
<!DOCTYPE html>
<html lang="en">
<head>
<meta charset="utf-8">
<title>Birchline Septic Solutions – Business Card</title>
<link href="https://fonts.googleapis.com/css2?family=Open+Sans:wght@400;600;700;800&display=swap" rel="stylesheet">
<style>
  :root {
    --backdrop: #232323;
    --card: #1e1e21;
    --card-edge: #2a2a2e;
    --teal: #2bbdb3;
    --white: #ffffff;
    --logo-dark: #0c0c0e;
  }
  * { box-sizing: border-box; margin: 0; padding: 0; }
  html, body {
    width: 1200px; height: 779px; overflow: hidden;
    background: var(--backdrop);
    font-family: "Open Sans", sans-serif;
  }
  .stage {
    position: relative; width: 1200px; height: 779px;
    display: flex; justify-content: center; align-items: center; gap: 80px;
  }
  .card {
    position: relative; width: 320px; height: 560px;
    background: var(--card);
    border-radius: 18px;
    border: 1px solid var(--card-edge);
    box-shadow: 0 18px 40px rgba(0,0,0,.55);
    overflow: hidden;
  }

  /* Front: name only */
  .card-front {
    display: flex; align-items: center; justify-content: center;
  }
  .front-name {
    color: var(--logo-dark);
    font-weight: 800;
    text-align: center;
    line-height: 1.05;
  }
  .front-name .line-main { display: block; font-size: 46px; }
  .front-name .line-sub { display: block; font-size: 46px; font-size: 15px; letter-spacing: 5px; margin-top: 8px; }

  /* Back: contact side */
  .brand {
    position: absolute; top: 58px; left: 0; right: 0;
    text-align: center; color: var(--white); font-weight: 800; line-height: 1;
  }
  .brand .line-main { display: block; font-size: 40px; letter-spacing: 1px; }
  .brand .line-sub { display: block; font-size: 11px; letter-spacing: 4px; margin-top: 10px; }

  .owner {
    position: absolute; top: 250px; left: 0; right: 0; text-align: center;
  }
  .owner-name { font-size: 26px; font-weight: 700; line-height: 1.1; }
  .owner-name .first { color: var(--teal); }
  .owner-name .last { color: var(--white); }
  .owner-city { color: var(--white); font-size: 14px; margin-top: 2px; }

  .divider {
    position: absolute; left: 28px; right: 28px; height: 2px;
    background: var(--teal);
  }
  .divider-phone { top: 326px; }
  .divider-services { top: 408px; }

  .phone {
    position: absolute; top: 346px; left: 0; right: 0;
    display: flex; justify-content: center; align-items: center; gap: 10px;
    color: var(--white); font-size: 21px; letter-spacing: .5px;
  }
  .phone-icon { width: 20px; height: 20px; flex: none; }

  .services-title {
    position: absolute; top: 420px; left: 0; right: 0; text-align: center;
    color: var(--teal); font-size: 13px; font-weight: 700; letter-spacing: 3px;
  }
  .services {
    position: absolute; top: 446px; left: 0; right: 0; text-align: center;
    list-style: none; color: var(--white); font-size: 14px; line-height: 1.35;
  }
</style>
</head>
<body>
<main class="stage">

  <section class="card card-front" aria-label="Card front">
    <p class="front-name">
      <span class="line-main">Birchline</span>
      <span class="line-sub">SEPTIC SOLUTIONS</span>
    </p>
  </section>

  <section class="card card-back" aria-label="Card back">
    <p class="brand">
      <span class="line-main">Birchline</span>
      <span class="line-sub">SEPTIC SOLUTIONS</span>
    </p>

    <div class="owner">
      <p class="owner-name"><span class="first">Colin</span> <span class="last">Vandro</span></p>
      <p class="owner-city">Harlow Springs, OH</p>
    </div>

    <div class="divider divider-phone"></div>

    <p class="phone">
      <svg class="phone-icon" viewBox="0 0 20 20" aria-hidden="true">
        <circle cx="10" cy="10" r="10" fill="var(--teal)"/>
        <path d="M6 5.5c.8-.8 1.6-.6 2 0l.8 1.3c.3.5.1 1-.3 1.3l-.6.4c.5 1.1 1.2 1.8 2.3 2.3l.4-.6c.3-.4.8-.6 1.3-.3l1.3.8c.6.4.8 1.2 0 2-1.3 1.3-3.4.5-5.3-1.4C5.9 9.4 5.1 7.3 6 5.5z" fill="var(--white)"/>
      </svg>
      <span>555-241-0387</span>
    </p>

    <div class="divider divider-services"></div>

    <p class="services-title">SERVICES</p>
    <ul class="services">
      <li>Installs</li>
      <li>Pumping</li>
      <li>Inspections</li>
      <li>And Repairs</li>
    </ul>
  </section>

</main>
</body>
</html>
```